Restyle corporate identity (+ logo) for a road construction company

We need a new logo and stationary design for our company VARNOK path. VARNOK path® increases the road base strength, while reducing major costs and time of road construction. Attached some examples of the current design.

Our wishes for the new logo:
- Business look
- Style sheet
- Modern

More information: www.varnokpath.example
Updates

Target Market(s)

Government

Industry/Entity Type

Construction

Requirements
Must have
• Logo (with road sign) + text

```html
<!DOCTYPE html>
<html lang="en">
<head>
<meta charset="utf-8">
<title>VARNOK path — Business Cards</title>
<link rel="stylesheet" href="https://fonts.googleapis.com/css2?family=Open+Sans:wght@400;600&display=swap">
<style>
  :root {
    --backdrop: #8f9091;
    --card: #f2f2f3;
    --brand-blue: #0a7ad8;
    --band-grey: #8a8b8d;
    --ink: #4a4b4d;
    --ink-soft: #8a8b8d;
    --divider: #c9c9cb;
  }
  * { margin: 0; padding: 0; box-sizing: border-box; }
  html, body { width: 1105px; height: 1200px; overflow: hidden; }
  body {
    background: var(--backdrop);
    font-family: "Open Sans", Arial, sans-serif;
    position: relative;
  }
  .card {
    position: absolute;
    left: 182px;
    width: 746px;
    height: 425px;
    background: var(--card);
    overflow: hidden;
  }
  .card--front { top: 120px; }
  .card--back { top: 637px; }

  .brand {
    position: absolute;
    display: flex;
    align-items: center;
    gap: 14px;
    color: var(--brand-blue);
    font-weight: 600;
  }
  .brand__mark {
    width: 24px; height: 24px;
    background: var(--brand-blue);
    flex: none;
  }
  .brand__name { line-height: 1.02; letter-spacing: 2px; }
  .card--front .brand { left: 70px; top: 168px; font-size: 40px; }
  .card--back .brand { left: 50%; top: 150px; transform: translateX(-50%); font-size: 54px; }

  .divider {
    position: absolute;
    left: 395px; top: 87px;
    width: 1px; height: 248px;
    background: var(--divider);
  }
  .contact { position: absolute; left: 426px; top: 88px; color: var(--ink); }
  .contact__name { font-size: 25px; font-weight: 600; color: var(--brand-blue); line-height: 32px; }
  .contact__role { font-size: 19px; color: var(--ink-soft); line-height: 26px; }
  .contact__address { margin-top: 20px; font-size: 19px; line-height: 26px; }
  .contact__lines { margin-top: 14px; list-style: none; font-size: 19px; line-height: 28px; }
  .contact__lines li { display: flex; align-items: center; gap: 10px; }
  .contact__lines svg { width: 18px; height: 18px; flex: none; fill: var(--brand-blue); }

  .band { position: absolute; left: 0; bottom: 0; width: 746px; height: 28px; }

  .web-address {
    position: absolute;
    left: 0; right: 0; top: 358px;
    text-align: center;
    font-size: 19px;
    letter-spacing: 4px;
    color: var(--ink);
  }
</style>
</head>
<body>

<section class="card card--front">
  <div class="brand">
    <span class="brand__mark"></span>
    <span class="brand__name">VARNOK<br>PATH</span>
  </div>

  <div class="divider"></div>

  <div class="contact">
    <p class="contact__name">Maren Kolde</p>
    <p class="contact__role">CEO/Founder</p>
    <p class="contact__address">Lindenkade 58<br>3012 KT Veldhaven<br>The Netherlands</p>
    <ul class="contact__lines">
      <li>
        <svg viewBox="0 0 24 24" aria-hidden="true"><path d="M6.6 10.8a15.1 15.1 0 0 0 6.6 6.6l2.2-2.2c.3-.3.7-.4 1-.2 1.1.4 2.3.6 3.6.6.6 0 1 .4 1 1V20c0 .6-.4 1-1 1A17 17 0 0 1 3 4c0-.6.4-1 1-1h3.5c.6 0 1 .4 1 1 0 1.3.2 2.5.6 3.6.1.3 0 .7-.2 1z"/></svg>
        612 480 3917
      </li>
      <li>
        <svg viewBox="0 0 24 24" aria-hidden="true"><path d="M2 5h20v14H2z M3.5 6.5 12 13l8.5-6.5" stroke="#f2f2f3" stroke-width="1.4"/></svg>
        contact@varnokpath.example
      </li>
      <li>
        <svg viewBox="0 0 24 24" aria-hidden="true"><circle cx="12" cy="12" r="10"/><path d="M2 12h20M12 2c3 3 3 17 0 20M12 2c-3 3-3 17 0 20" stroke="#f2f2f3" stroke-width="1.3" fill="none"/></svg>
        www.varnokpath.example
      </li>
    </ul>
  </div>

  <svg class="band" viewBox="0 0 746 28" preserveAspectRatio="none" aria-hidden="true">
    <polygon points="0,0 492,0 484,28 0,28" fill="var(--brand-blue)"/>
    <polygon points="497,0 746,0 746,28 489,28" fill="var(--band-grey)"/>
  </svg>
</section>

<section class="card card--back">
  <div class="brand">
    <span class="brand__mark"></span>
    <span class="brand__name">VARNOK<br>PATH</span>
  </div>
  <p class="web-address">www.varnokpath.example</p>
</section>

</body>
</html>
```